Law Firm Header Revision

Task: Redesign my law firm Word document header (modern, succinct, logo-first, easy address updates)

I need you to revise and modernize my Microsoft Word document header for Law Office of Bram Holcott, PLLC. The result should look professional and clean on letters (including Letters of Protection), with the logo as the main focus and the text kept succinct.

Goals:
1. Create a modern, minimal header that feels premium and uncluttered.
Make the logo the most visually dominant element.
Reduce the visual weight of the contact/address block so it doesn’t distract from the document.
Make the address easy to change later (I’m moving offices soon) while keeping the same header design.

2. Content to include (keep all info accurate):
Law Office of Bram Holcott, PLLC
615 Pemberly St. Ste #300-214, Houston, TX 77002
Office: 832.555.0143
Direct: 713.555.0187
Fax: 832.555.0129
Bholcottlaw.com

3. Layout requirements:
Provide 3 header style options:
Logo left + contact info right
Centered logo + single concise contact line below
Logo left + firm name prominent + minimal contact line
The primary line near the logo should be minimal (preferably website + main office phone).
The address should be easy to update in one place without redesigning the header. Prefer either:
Move the full address to the footer, or
Put the address in a single dedicated line/block so I can edit it once and keep the layout unchanged.
4. Build constraints:
Must be achievable using standard Microsoft Word tools only (header/footer, tables, alignment, fonts, spacing). No advanced graphics software.
Provide exact header text, plus step-by-step Word instructions for each option:
Font recommendations + sizes
Alignment
Spacing
Table setup (if used)
How to keep it consistent across pages

5. Deliverable:
For each of the 3 options, provide:
The exact header content (with line breaks)
Formatting specs (fonts, sizes, spacing)
Word build steps so I can recreate it reliably and keep the logo as the focal point.

```html
<!DOCTYPE html>
<html lang="en">
<head>
<meta charset="utf-8">
<title>Bram Holcott Law – Letterhead Options</title>
<link rel="stylesheet" href="https://fonts.googleapis.com/css2?family=Mulish:wght@400;600;700&family=Roboto:wght@400;500;700&family=Libre+Baskerville&display=swap">
<style>
  :root {
    --navy: #0c1628;
    --band-grey: #d6d6d6;
    --mark-grey: #e9ecee;
    --stage: #d3d3d3;
    --paper: #ffffff;
  }
  html, body { margin: 0; padding: 0; overflow: hidden; }
  body { width: 1200px; height: 554px; background: var(--stage); position: relative; }
  .letterhead {
    position: absolute; top: 26px; width: 356px; height: 503px;
    background: var(--paper); box-shadow: 0 2px 6px rgba(0,0,0,.25);
  }
  .letterhead svg { display: block; width: 100%; height: 100%; }
  .option-logo-right { left: 35px; }
  .option-centered { left: 422px; }
  .option-firm-name { left: 809px; }
  .name { font-family: "Mulish", sans-serif; font-weight: 700; fill: var(--navy); letter-spacing: .5px; }
  .contact { font-family: "Roboto", sans-serif; font-size: 13px; }
  .contact-bold { font-weight: 700; }
  .on-dark { fill: #fff; }
  .on-light { fill: var(--navy); }
  .foot { font-family: "Mulish", sans-serif; fill: #fff; }
  .foot-title { font-size: 12px; font-weight: 700; }
  .foot-line { font-size: 11px; }
  .doc-label { font-family: "Libre Baskerville", serif; font-size: 10px; fill: #fff; }
  .page-num { font-family: "Libre Baskerville", serif; fill: #fff; }
</style>
</head>
<body>

<svg width="0" height="0" style="position:absolute">
  <defs>
    <symbol id="icon-phone" viewBox="0 0 24 24"><path d="M6.6 10.8a15 15 0 0 0 6.6 6.6l2.2-2.2c.3-.3.7-.4 1-.2 1.1.4 2.3.6 3.6.6.6 0 1 .4 1 1V20c0 .6-.4 1-1 1A17 17 0 0 1 3 4c0-.6.4-1 1-1h3.5c.6 0 1 .4 1 1 0 1.3.2 2.5.6 3.6.1.3 0 .7-.2 1z"/></symbol>
    <symbol id="icon-globe" viewBox="0 0 24 24"><circle cx="12" cy="12" r="9" fill="none" stroke="currentColor" stroke-width="2"/><path d="M3 12h18M12 3c3 3 3 15 0 18M12 3c-3 3-3 15 0 18" fill="none" stroke="currentColor" stroke-width="2"/></symbol>
    <symbol id="icon-pin" viewBox="0 0 24 24"><path d="M12 2a7 7 0 0 0-7 7c0 5 7 13 7 13s7-8 7-13a7 7 0 0 0-7-7zm0 9.5A2.5 2.5 0 1 1 12 6.5a2.5 2.5 0 0 1 0 5z"/></symbol>
    <g id="site-footer">
      <rect x="0" y="952" width="765" height="2" fill="var(--navy)"/>
      <rect x="0" y="958" width="765" height="122" fill="var(--navy)"/>
      <circle cx="383" cy="958" r="20" fill="var(--navy)"/>
      <circle cx="62" cy="1007" r="13" fill="#fff"/>
      <use href="#icon-pin" x="54" y="999" width="16" height="16" fill="var(--navy)"/>
      <text class="foot foot-title" x="85" y="1003">Law Office of Bram Holcott, PLLC</text>
      <text class="foot foot-line" x="85" y="1019">615 Pemberly St. Ste #300-214, Houston, TX 77002</text>
      <circle cx="411" cy="1007" r="13" fill="#fff"/>
      <use href="#icon-phone" x="404" y="1000" width="14" height="14" fill="var(--navy)"/>
      <text class="foot foot-line" x="433" y="1011">Direct: 713.555.0187</text>
      <circle cx="596" cy="1007" r="13" fill="#fff"/>
      <use href="#icon-phone" x="589" y="1000" width="14" height="14" fill="var(--navy)"/>
      <text class="foot foot-line" x="618" y="1011">Fax: 832.555.0129</text>
      <text class="doc-label" x="38" y="1054">LETTERS OF PROTECTION</text>
      <text class="page-num" x="728" y="1054" text-anchor="end"><tspan font-size="10">PAGE : </tspan><tspan font-size="15">1</tspan></text>
    </g>
  </defs>
</svg>

<!-- Option 1: logo left, contact right -->
<section class="letterhead option-logo-right">
  <svg viewBox="0 0 765 1080">
    <rect x="38" y="12" width="38" height="38" fill="var(--navy)"/>
    <text class="name" x="86" y="42" font-size="26">BRAM HOLCOTT</text>
    <polygon points="425,8 468,8 490,0 765,0 765,25 488,25" fill="var(--navy)"/>
    <polygon points="488,25 765,25 765,57 505,57 475,40" fill="var(--band-grey)"/>
    <polygon points="475,45 505,57 765,57 765,63 503,63" fill="var(--navy)"/>
    <circle cx="404" cy="35" r="4" fill="var(--navy)"/>
    <rect x="404" y="34" width="50" height="2" fill="var(--navy)"/>
    <use href="#icon-phone" x="535" y="6" width="14" height="14" fill="#fff"/>
    <text class="contact contact-bold on-dark" x="563" y="18">Office: 832.555.0143</text>
    <use href="#icon-globe" x="535" y="34" width="14" height="14" color="var(--navy)"/>
    <text class="contact contact-bold on-light" x="563" y="46">Website: Bholcottlaw.com</text>
    <rect x="229" y="393" width="307" height="294" fill="var(--mark-grey)"/>
    <use href="#site-footer"/>
  </svg>
</section>

<!-- Option 2: centered logo, single contact line -->
<section class="letterhead option-centered">
  <svg viewBox="0 0 765 1080">
    <polygon points="0,0 98,60 40,60 0,105" fill="var(--navy)"/>
    <polygon points="40,60 765,60 765,92 145,92 135,102 0,106" fill="var(--band-grey)"/>
    <polygon points="145,94 765,94 765,102 135,102" fill="var(--navy)"/>
    <rect x="293" y="12" width="38" height="38" fill="var(--navy)"/>
    <text class="name" x="340" y="42" font-size="26">BRAM HOLCOTT</text>
    <use href="#icon-globe" x="232" y="67" width="14" height="14" color="var(--navy)"/>
    <text class="contact on-light" x="254" y="78">Website: Bholcottlaw.com</text>
    <use href="#icon-phone" x="432" y="67" width="14" height="14" fill="var(--navy)"/>
    <text class="contact on-light" x="455" y="78">Office: 832.555.0143</text>
    <rect x="274" y="436" width="217" height="208" fill="var(--mark-grey)"/>
    <use href="#site-footer"/>
  </svg>
</section>

<!-- Option 3: logo left, firm name prominent -->
<section class="letterhead option-firm-name">
  <svg viewBox="0 0 765 1080">
    <rect x="38" y="18" width="38" height="38" fill="var(--navy)"/>
    <text class="name" x="86" y="48" font-size="26">BRAM HOLCOTT</text>
    <polygon points="0,75 212,75 234,38 248,38 220,88 0,88" fill="var(--navy)"/>
    <polygon points="252,38 262,38 238,86 228,86" fill="var(--band-grey)"/>
    <polygon points="268,48 765,48 765,78 250,78" fill="var(--navy)"/>
    <circle cx="327" cy="23" r="13" fill="var(--mark-grey)"/>
    <use href="#icon-phone" x="320" y="16" width="14" height="14" fill="var(--navy)"/>
    <text class="contact on-light" x="350" y="28"><tspan class="contact-bold">Office:</tspan> 832.555.0143</text>
    <circle cx="517" cy="23" r="13" fill="var(--mark-grey)"/>
    <use href="#icon-globe" x="510" y="16" width="14" height="14" color="var(--navy)"/>
    <text class="contact on-light" x="540" y="28"><tspan class="contact-bold">Website:</tspan> Bholcottlaw.com</text>
    <text class="contact contact-bold on-dark" x="480" y="67" text-anchor="middle" font-size="14">Law Office of Bram Holcott, PLLC</text>
    <rect x="229" y="393" width="307" height="294" fill="var(--mark-grey)"/>
    <use href="#site-footer"/>
  </svg>
</section>

</body>
</html>
```